DLM TAX & ACCOUNTING business card
Income tax, audit, bookkeeping, setup, training and services
Professional
Marcus Elden Trabb
47 Quillmore Road
Toronto, ON K7R 4B8
dlm_tax@mailvex.ca

```html
<!DOCTYPE html>
<html lang="en">
<head>
<meta charset="utf-8">
<title>DLM Tax &amp; Accounting – Business Card</title>
<link rel="stylesheet" href="https://fonts.googleapis.com/css2?family=Montserrat:wght@800&family=Open+Sans:wght@400;600&display=swap">
<style>
  :root {
    --page: #e9e9e9;
    --card: #ffffff;
    --green: #7dc61e;
    --green-dark: #5a9a0c;
    --ink: #2b2b2b;
    --white: #ffffff;
  }
  html, body {
    margin: 0;
    padding: 0;
    overflow: hidden;
  }
  body {
    width: 1200px;
    height: 864px;
    background: var(--page);
    position: relative;
    font-family: "Open Sans", sans-serif;
  }
  .card {
    position: absolute;
    top: 282px;
    width: 520px;
    height: 300px;
    border-radius: 18px;
    background: var(--card);
    overflow: hidden;
    box-shadow: 0 6px 18px rgba(0,0,0,0.18);
  }
  .card--front { left: 50px; }
  .card--back  { left: 630px; }

  .brand-name {
    font-family: "Montserrat", sans-serif;
    font-weight: 800;
    color: var(--ink);
    margin: 0;
    letter-spacing: 0.5px;
  }
  .card--front .brand-name {
    position: absolute;
    left: 0;
    right: 0;
    top: 128px;
    text-align: center;
    font-size: 30px;
  }

  .back-art {
    position: absolute;
    inset: 0;
  }
  .card--back .brand-name {
    position: absolute;
    left: 26px;
    top: 140px;
    font-size: 18px;
    width: 190px;
    line-height: 1.25;
  }
  .holder-name {
    position: absolute;
    left: 26px;
    top: 196px;
    margin: 0;
    font-size: 13px;
    font-weight: 600;
    color: var(--green-dark);
  }
  .contact-list {
    position: absolute;
    right: 24px;
    top: 58px;
    margin: 0;
    padding: 0;
    list-style: none;
    color: var(--white);
    font-size: 12px;
    line-height: 1.25;
  }
  .contact-list li {
    display: flex;
    align-items: flex-start;
    gap: 8px;
    margin-bottom: 9px;
  }
  .contact-icon {
    flex: 0 0 16px;
    width: 16px;
    height: 16px;
    margin-top: 1px;
  }
</style>
</head>
<body>

  <section class="card card--front">
    <h1 class="brand-name">DLM TAX &amp; ACCOUNTING</h1>
  </section>

  <section class="card card--back">
    <svg class="back-art" viewBox="0 0 520 300" width="520" height="300" aria-hidden="true">
      <path d="M280,0 C212,120 210,222 96,300 L520,300 L520,0 Z" fill="#111"/>
      <path d="M292,0 C224,120 222,222 110,300 L520,300 L520,0 Z" fill="#fff"/>
      <path d="M302,0 C236,120 234,222 124,300 L520,300 L520,0 Z" fill="var(--green)"/>
    </svg>

    <h2 class="brand-name">DLM TAX &amp; ACCOUNTING</h2>
    <p class="holder-name">Marcus Elden Trabb</p>

    <ul class="contact-list">
      <li>
        <svg class="contact-icon" viewBox="0 0 16 16"><circle cx="8" cy="8" r="8" fill="#fff"/><path d="M8 3.5a2.6 2.6 0 0 0-2.6 2.6C5.4 8 8 12 8 12s2.6-4 2.6-5.9A2.6 2.6 0 0 0 8 3.5z" fill="var(--green)"/><circle cx="8" cy="6.1" r="1" fill="#fff"/></svg>
        <span>47 Quillmore Road<br>Toronto, ON K7R 4B8</span>
      </li>
      <li>
        <svg class="contact-icon" viewBox="0 0 16 16"><circle cx="8" cy="8" r="8" fill="#fff"/><path d="M5.2 4.2l1.5-.4 1 2.2-1 .8a5 5 0 0 0 2.5 2.5l.8-1 2.2 1-.4 1.5c-3.6.3-7-3.1-6.6-6.6z" fill="var(--green)"/></svg>
        <span>416-555-0187</span>
      </li>
      <li>
        <svg class="contact-icon" viewBox="0 0 16 16"><circle cx="8" cy="8" r="8" fill="#fff"/></svg>
        <span>dlm_tax</span>
      </li>
      <li>
        <svg class="contact-icon" viewBox="0 0 16 16"><circle cx="8" cy="8" r="8" fill="#fff"/><rect x="4" y="5" width="8" height="6" rx="0.8" fill="var(--green)"/><path d="M4.3 5.4L8 8.3l3.7-2.9" fill="none" stroke="#fff" stroke-width="0.9"/></svg>
        <span>dlm_tax@mailvex.ca</span>
      </li>
      <li>
        <svg class="contact-icon" viewBox="0 0 16 16"><circle cx="8" cy="8" r="8" fill="#fff"/><circle cx="8" cy="8" r="4.2" fill="none" stroke="var(--green)" stroke-width="1"/><ellipse cx="8" cy="8" rx="1.8" ry="4.2" fill="none" stroke="var(--green)" stroke-width="0.9"/><path d="M3.8 8h8.4" stroke="var(--green)" stroke-width="0.9"/></svg>
        <span>www.dlmledger.ca</span>
      </li>
    </ul>
  </section>

</body>
</html>
```